Business Intelligence Application - Reporting Menu and Report Criteria Design

Looking for a fresh, effective and user friendly view for the menu structure and reporting criteria screen format for a business reporting application. Initial format completed, content structure is in place, but we need the 'wow' design.. as its a serious professional report/BI tool it has to fall within certain guidelines for clarity and graphics..but we want it to be slick, friendly, great user experience. There is a large amount of complex content to fit into a small space and we need it to be very inviting, modern and intuitive.. If interested, please review the attachment. We have live screens in operation, but feel these could be improved and looking forward to seeing what great creative suggestions could be made. Please review work done to date in the attached.. We are not looking for a total re-design of everything, all the basic business content/structure is there.. but tell us what we could do to improve this in terms of graphic design... particularly the criteria screens.. thanks!
Updates

Reason: Need a few more days to review designs - thanks for all submissions so far, we will make a selection shortly.

Target Market(s)

Business analysts, hotel operations teams, finance analysts hospitality industry

Industry/Entity Type

Hospitality

Coding

Coded - Design and coding required

Number of Pages Required

4 page

Font styles to use
Sans Serif
Other font styles liked:
• Candara, please see example in deck

Colors
3276b5
3176b5
0255a3
85acd3
33a6d7
cee9f5
85cae6

Requirements
Must have
• sharp clear, logical menu structure, (currently it has 'clicks to sub-menus, we need hover over, slide to sub-menus..) colour, styling.. and most focus on revision of criteria.. right now is somewhat heavy, cumbersome.. keep colour and friendly intuitive process steps.. its heavy analytical stuff.. best of luck!
Should not have
• No grey fonts on white or grey screens! many business apps are not readable or sharp.. or fonts are too small.. colourless, so please avoid that.. see our deck - sharp dark (navy) or black fonts on white, or light shading..

```html
<!DOCTYPE html>
<html lang="en">
<head>
<meta charset="utf-8">
<title>RevSight – Property Search</title>
<link rel="stylesheet" href="https://fonts.googleapis.com/css2?family=Open+Sans:ital,wght@0,400;0,600;1,400&display=swap">
<style>
:root{
  --navy:#0255a3;
  --blue:#3276b5;
  --divider:#5a8fc4;
  --page:#eaf2f7;
  --field-border:#cee9f5;
  --row-border:#d6e6f1;
  --head-bg:#f4f8fb;
  --ink:#0255a3;
  --text:#555d66;
  --white:#ffffff;
}
*{box-sizing:border-box;margin:0;padding:0}
html,body{width:1200px;height:656px;overflow:hidden}
body{font-family:"Open Sans",Arial,sans-serif;background:var(--page);position:relative}
.topbar{position:absolute;left:0;top:0;width:1200px;height:80px;background:var(--navy);color:var(--white)}
.brand{position:absolute;left:22px;top:14px;font-size:38px;font-weight:400;line-height:48px;letter-spacing:.5px}
.welcome{position:absolute;right:165px;top:22px;text-align:right}
.welcome-name{font-size:16px;line-height:20px}
.welcome-date{font-size:9.5px;font-style:italic;line-height:14px}
.avatar{position:absolute;left:1045px;top:24px;width:32px;height:32px;border-radius:50%;background:radial-gradient(circle at 50% 40%,#d9b79a,#8a6a55);border:2px solid #e9eef3}
.top-btn{position:absolute;top:24px;width:32px;height:32px;border-radius:50%;background:#eaf2f7;display:flex;align-items:center;justify-content:center}
.top-btn.bell{left:1101px}.top-btn.exit{left:1144px}
.sidebar{position:absolute;left:0;top:80px;width:240px;height:576px;background:var(--blue)}
.nav-item{height:80px;border-bottom:1px solid var(--divider);display:flex;align-items:center;color:var(--white);font-size:17px}
.nav-item.active{background:var(--navy);border-bottom-color:var(--navy)}
.nav-icon{width:16px;height:16px;margin:0 17px 0 25px}
.main{position:absolute;left:240px;top:80px;width:960px;height:576px}
.page-title{position:absolute;left:22px;top:28px;font-size:35px;font-weight:600;color:var(--ink);line-height:46px}
.field{position:absolute;width:280px}
.field label{display:block;font-size:14.5px;color:var(--ink);line-height:18px;margin-bottom:8px}
.field .input{height:43px;background:var(--white);border:1px solid var(--field-border);font-size:12px;color:#3a4450;padding:0 16px;line-height:41px}
.results{position:absolute;left:24px;top:291px;width:910px;border:1px solid var(--field-border);background:var(--white)}
.results-head{height:44px;background:var(--head-bg);color:var(--ink);font-size:14.5px;line-height:44px;padding-left:15px}
.results table{width:100%;border-collapse:collapse;font-size:14.5px;color:var(--text)}
.results td{border-top:1px solid var(--row-border);padding-left:16px}
.results td.code{border-left:1px solid var(--row-border);padding-left:88px;width:455px}
.copyright{position:absolute;left:0;width:720px;top:537px;text-align:center;font-size:11.5px;color:var(--ink)}
.page-code{position:absolute;right:11px;top:552px;font-size:11px;color:var(--ink)}
</style>
</head>
<body>
<header class="topbar">
  <div class="brand">RevSight</div>
  <div class="welcome">
    <div class="welcome-name">Welcome Admin</div>
    <div class="welcome-date">Tuesday 5 October, 2017</div>
  </div>
  <div class="avatar" role="img" aria-label="Admin profile photo"></div>
  <div class="top-btn bell"><svg width="14" height="14" viewBox="0 0 16 16"><path d="M8 1a1.3 1.3 0 0 1 1.3 1.3A4.5 4.5 0 0 1 12.5 7v3.5L14 12v1H2v-1l1.5-1.5V7a4.5 4.5 0 0 1 3.2-4.7A1.3 1.3 0 0 1 8 1zM6.3 14h3.4a1.7 1.7 0 0 1-3.4 0z" fill="#0255a3"/></svg></div>
  <div class="top-btn exit"><svg width="14" height="14" viewBox="0 0 16 16"><path d="M1 6.5h6V4l4 4-4 4V9.5H1z M9 2h5v12H9v-2h3V4H9z" fill="#0255a3"/></svg></div>
</header>

<nav class="sidebar">
  <div class="nav-item"><svg class="nav-icon" viewBox="0 0 16 16"><circle cx="8" cy="4.5" r="3.5" fill="#fff"/><path d="M2 15c0-4 2.5-6 6-6s6 2 6 6z" fill="#fff"/></svg>Admin</div>
  <div class="nav-item"><svg class="nav-icon" viewBox="0 0 16 16"><circle cx="8" cy="5" r="2.6" fill="#fff"/><circle cx="3.3" cy="5.5" r="1.9" fill="#fff"/><circle cx="12.7" cy="5.5" r="1.9" fill="#fff"/><path d="M3.5 14c0-3.5 2-5 4.5-5s4.5 1.5 4.5 5z M0 12c0-2.5 1.3-3.8 3.3-3.8 1 0 1 .5 1 .5-1 1-1.3 2-1.3 3.3z M16 12c0-2.5-1.3-3.8-3.3-3.8-1 0-1 .5-1 .5 1 1 1.3 2 1.3 3.3z" fill="#fff"/></svg>Mangement</div>
  <div class="nav-item"><svg class="nav-icon" viewBox="0 0 16 16"><path d="M0 8c2-3.5 5-5 8-5s6 1.5 8 5c-2 3.5-5 5-8 5S2 11.5 0 8z" fill="#fff"/><circle cx="8" cy="8" r="3" fill="#3276b5"/><circle cx="8" cy="8" r="1.4" fill="#fff"/></svg>My View</div>
  <div class="nav-item active"><svg class="nav-icon" viewBox="0 0 16 16"><circle cx="6.5" cy="6.5" r="4.8" fill="none" stroke="#fff" stroke-width="2.4"/><path d="M10 10l4.5 4.5" stroke="#fff" stroke-width="2.8" stroke-linecap="round"/></svg>Property Search</div>
  <div class="nav-item"><svg class="nav-icon" viewBox="0 0 16 16"><circle cx="6" cy="9" r="4.2" fill="none" stroke="#fff" stroke-width="2.6" stroke-dasharray="2.2 1.1"/><circle cx="6" cy="9" r="1.4" fill="#fff"/><circle cx="12.5" cy="4" r="2.6" fill="none" stroke="#fff" stroke-width="1.8" stroke-dasharray="1.6 1"/><circle cx="12.5" cy="12.5" r="2" fill="none" stroke="#fff" stroke-width="1.6"/></svg>Intel</div>
  <div class="nav-item"><svg class="nav-icon" viewBox="0 0 16 16"><path d="M8 1.5a4.5 4.5 0 0 0-2.6 8.2V12h5.2V9.7A4.5 4.5 0 0 0 8 1.5z" fill="none" stroke="#fff" stroke-width="1.6"/><rect x="6" y="13.2" width="4" height="1.6" rx=".6" fill="#fff"/></svg>Planning</div>
</nav>

<main class="main">
  <h1 class="page-title">Property Search</h1>

  <div class="field" style="left:24px;top:100px"><label>Search Name</label><div class="input">Royal...</div></div>
  <div class="field" style="left:340px;top:100px"><label>Search ID</label><div class="input"></div></div>
  <div class="field" style="left:655px;top:100px"><label>Search Product</label><div class="input"></div></div>

  <div class="field" style="left:24px;top:196px"><label>Divisions</label><div class="input">North America</div></div>
  <div class="field" style="left:340px;top:196px"><label>Regions</label><div class="input"></div></div>
  <div class="field" style="left:655px;top:196px"><label>Areas</label><div class="input"></div></div>

  <section class="results">
    <div class="results-head">Select Property</div>
    <table>
      <tr style="height:43px"><td>Harbor View Hotel &amp; Towers</td><td class="code">RHDOH</td></tr>
      <tr style="height:48px"><td>Coral Shore Hotel</td><td class="code">123</td></tr>
      <tr style="height:40px"><td>Aliquam erat volutpat</td><td class="code">Pellentesque</td></tr>
      <tr style="height:40px"><td>Quisque aliquet ex nec est</td><td class="code">Aenean</td></tr>
    </table>
  </section>

  <p class="copyright">Copyright &nbsp;©&nbsp; 2017 &nbsp;RevSight. &nbsp;All rights reserved.</p>
  <span class="page-code">M2</span>
</main>
</body>
</html>
```